Tech business card design

We need an amazing business card design for our new business 'Pexla' a marketing tech startup based in Sydney, Australia. We provide an online marketplace for businesses to search and buy advertising media, connect with service providers and learn more about marketing. We wish to communicate 'cool tech', reliability and professionalism and design based around our logo.

Target Market(s)

Business Owners

Contact Information for Business Card

Name
Position
Email Address
Website
Phone Number

Font styles to use
Other font styles liked:
• Avenir & Avenir Next

Colors

Designer to choose colors to be used in the design.

```html
<!DOCTYPE html>
<html lang="en">
<head>
<meta charset="utf-8">
<title>Pexla Business Card</title>
<link rel="stylesheet" href="https://fonts.googleapis.com/css2?family=Nunito+Sans:wght@400;700;800&display=swap">
<style>
  :root {
    --stage: #1c1c1e;
    --paper: #ffffff;
    --navy: #1b2350;
    --ink: #1d1f2b;
    --rule-grey: #7a7a7a;
    --band-line: #b9bcc6;
  }
  * { box-sizing: border-box; margin: 0; padding: 0; }
  html, body {
    width: 1200px;
    height: 803px;
    overflow: hidden;
    background: var(--stage);
    font-family: "Nunito Sans", Arial, sans-serif;
    color: var(--ink);
  }
  .stage {
    position: relative;
    width: 1200px;
    height: 803px;
    display: flex;
    align-items: center;
    justify-content: center;
    gap: 60px;
  }
  .card {
    position: relative;
    width: 520px;
    height: 300px;
    background: var(--paper);
    overflow: hidden;
  }
  .wordmark {
    position: absolute;
    font-weight: 800;
    color: var(--navy);
    letter-spacing: -0.02em;
    line-height: 1;
  }
  .wordmark .tm {
    font-size: 0.16em;
    font-weight: 800;
    vertical-align: top;
    margin-left: 0.12em;
    letter-spacing: 0;
  }

  /* Front: contact side */
  .card-front .wordmark {
    left: 128px;
    top: 36px;
    font-size: 74px;
  }
  .card-front .divider-grey {
    position: absolute;
    left: 118px;
    top: 182px;
    width: 140px;
    height: 4px;
    background: var(--rule-grey);
  }
  .card-front .divider-navy {
    position: absolute;
    left: 258px;
    top: 183px;
    right: 0;
    height: 1.5px;
    background: var(--navy);
  }
  .card-front .address {
    position: absolute;
    right: 26px;
    top: 138px;
    text-align: right;
    font-size: 12px;
    line-height: 1.35;
  }
  .card-front .holder {
    position: absolute;
    left: 120px;
    top: 140px;
  }
  .holder .name {
    font-size: 15px;
    font-weight: 800;
    color: var(--navy);
    letter-spacing: 0.02em;
  }
  .holder .position {
    font-size: 11px;
    font-weight: 700;
  }
  .contacts {
    position: absolute;
    left: 136px;
    top: 198px;
    list-style: none;
    font-size: 13px;
    line-height: 1.45;
  }
  .contacts li {
    display: flex;
    align-items: center;
    gap: 8px;
  }
  .contacts svg {
    width: 11px;
    height: 11px;
    fill: var(--ink);
    flex: none;
  }

  /* Back: logo side */
  .card-back .wordmark {
    left: 50%;
    top: 96px;
    transform: translateX(-50%);
    font-size: 104px;
    white-space: nowrap;
  }
  .card-back .band-line {
    position: absolute;
    left: 0;
    right: 0;
    bottom: 42px;
    height: 2px;
    background: var(--band-line);
  }
  .card-back .band {
    position: absolute;
    left: 0;
    right: 0;
    bottom: 0;
    height: 38px;
    background: var(--navy);
  }
</style>
</head>
<body>
  <main class="stage">
    <section class="card card-front" aria-label="Business card, contact side">
      <div class="wordmark">pexla<span class="tm">TM</span></div>
      <p class="address">Street Name, City Name<br>Zipcode:012345</p>
      <div class="holder">
        <p class="name">JOHN SMITH</p>
        <p class="position">Position</p>
      </div>
      <div class="divider-grey"></div>
      <div class="divider-navy"></div>
      <ul class="contacts">
        <li>
          <svg viewBox="0 0 24 24" aria-hidden="true"><path d="M6.6 10.8a15 15 0 0 0 6.6 6.6l2.2-2.2c.3-.3.7-.4 1-.2 1.1.4 2.3.6 3.6.6.6 0 1 .4 1 1V20c0 .6-.4 1-1 1C10.6 21 3 13.4 3 4c0-.6.4-1 1-1h3.5c.6 0 1 .4 1 1 0 1.3.2 2.5.6 3.6.1.3 0 .7-.2 1z"/></svg>
          012-345-6789
        </li>
        <li>
          <svg viewBox="0 0 24 24" aria-hidden="true"><path d="M2 5h20v14H2z M4 7v.5l8 5.5 8-5.5V7z" fill-rule="evenodd"/></svg>
          info@pexla.com
        </li>
        <li>
          <svg viewBox="0 0 24 24" aria-hidden="true"><path d="M12 2a10 10 0 1 0 0 20 10 10 0 0 0 0-20zm0 2c.9 1.2 1.6 2.6 2 4h-4c.4-1.4 1.1-2.8 2-4zM4.3 14a8 8 0 0 1 0-4h3.4a16 16 0 0 0 0 4zm.8 2h3c.3 1.3.8 2.5 1.4 3.6A8 8 0 0 1 5.1 16zm3-8h-3a8 8 0 0 1 4.4-3.6C8.9 5.5 8.4 6.7 8.1 8zM12 20c-.9-1.2-1.6-2.6-2-4h4c-.4 1.4-1.1 2.8-2 4zm2.3-6H9.7a14 14 0 0 1 0-4h4.6a14 14 0 0 1 0 4zm.2 5.6c.6-1.1 1.1-2.3 1.4-3.6h3a8 8 0 0 1-4.4 3.6zm1.8-5.6a16 16 0 0 0 0-4h3.4a8 8 0 0 1 0 4z"/></svg>
          www.pexla.com
        </li>
      </ul>
    </section>

    <section class="card card-back" aria-label="Business card, brand side">
      <div class="wordmark">pexla<span class="tm">TM</span></div>
      <div class="band-line"></div>
      <div class="band"></div>
    </section>
  </main>
</body>
</html>
```